Brimlow OrthoLink IT Inc. new website

i need a website for my company which is dedicated to installation and service of computer systems in Dental Offices. I would like for it to encompass a technology feel and professional look. The company deals with all aspects of technology like, Audio Visual, computer systems and networks, Cloud services like data backup, data center. We provide manage services, support and services to Dental Professionals.
Updates

Looking for a Technology font but professional look Added Wednesday, April 20, 2016

Target Market(s)

Dental, Dentist

Industry/Entity Type

Dental

Number of Pages Required

5+ page

Font styles to use
Other font styles liked:
• Futuristic or Techy

Colors
0255a3
ec1f27

Requirements
Must have
• Tabs
Nice to have
• Have no idea maybe some suggestion on your part may help
Should not have
• A professional feel but have a techy look

```html
<!DOCTYPE html>
<html lang="en">
<head>
<meta charset="utf-8">
<title>Brimlow OrthoLink IT Inc.</title>
<link rel="stylesheet" href="https://fonts.googleapis.com/css2?family=Roboto:wght@300;400;500;700;900&display=swap">
<style>
:root{
  --blue:#0255a3;
  --blue-dark:#01407c;
  --red:#ec1f27;
  --ink:#2b2b2b;
  --muted:#7a7a7a;
  --light:#f3f4f6;
  --line:#e3e3e3;
  --footer:#24272c;
  --footer-text:#b9bcc2;
  --white:#ffffff;
}
*{box-sizing:border-box;margin:0;padding:0}
html,body{width:1200px;height:2496px;overflow:hidden}
body{font-family:"Roboto",Arial,sans-serif;color:var(--ink);background:var(--white);position:relative}
p{line-height:1.6}

/* header */
.site-header{height:120px;position:relative}
.brand{position:absolute;left:100px;top:34px;display:flex;align-items:center;gap:12px}
.brand-mark{width:40px;height:40px;border-radius:50%;background:var(--blue)}
.brand-name{font-size:24px;font-weight:700;color:var(--blue);line-height:1.1;width:190px}
.search{position:absolute;left:620px;top:46px;width:260px;height:30px;border:1px solid var(--line);display:flex;align-items:center;padding:0 10px;font-size:12px;color:#aaa;justify-content:space-between}
.contact-top{position:absolute;right:100px;top:40px;display:flex;align-items:center;gap:14px;text-align:right}
.contact-top strong{display:block;font-size:15px;font-weight:500;color:var(--ink)}
.contact-top span{font-size:13px;color:var(--muted)}
.round-icon{width:40px;height:40px;border-radius:50%;background:var(--blue);display:flex;align-items:center;justify-content:center}

/* nav */
.main-nav{height:48px;background:var(--blue);padding:0 100px;display:flex}
.main-nav a{color:var(--white);text-decoration:none;font-size:14px;font-weight:500;padding:0 28px;line-height:48px;letter-spacing:.5px}
.main-nav a.active{background:var(--blue-dark)}

/* hero */
.hero{height:532px;position:relative;background:linear-gradient(100deg,#6d8eaa 0%,#b7c9d8 35%,#e9eef3 60%,#cfd9e2 100%)}
.hero-copy{position:absolute;left:168px;top:190px;color:var(--white)}
.hero-copy h1{font-size:40px;font-weight:700;line-height:1.2;text-transform:uppercase;width:520px}
.hero-copy p{font-size:15px;width:360px;margin-top:14px}
.hero-arrow{position:absolute;top:244px;width:36px;height:44px;background:rgba(0,0,0,.35);display:flex;align-items:center;justify-content:center}
.hero-arrow.prev{left:0}.hero-arrow.next{right:0}

/* services */
.services{padding:60px 100px 0;height:1200px - 700px}
.services-head{display:flex;gap:60px;align-items:flex-start}
.services-head h2{font-size:32px;font-weight:500;color:var(--blue);white-space:nowrap;border-bottom:3px solid var(--red);padding-bottom:8px}
.services-head p{font-size:13px;color:var(--muted)}
.service-cards{display:flex;gap:44px;margin-top:46px}
.service-card{width:304px}
.service-photo{height:192px;border-bottom:4px solid var(--blue)}
.service-card h3{font-size:20px;font-weight:400;margin-top:22px}
.service-card .row{display:flex;justify-content:space-between;align-items:center;margin-top:8px}
.service-card p{font-size:12px;color:var(--muted);width:250px}

/* welcome */
.welcome{position:absolute;top:1200px;left:0;width:1200px;height:340px;background:var(--red);color:var(--white);text-align:center;padding-top:66px}
.welcome h2{font-size:38px;font-weight:500;letter-spacing:1px}
.welcome p{font-size:13px;width:1000px;margin:22px auto 0;opacity:.92}
.btn-outline{display:inline-block;margin-top:28px;border:2px solid var(--white);color:var(--white);font-size:13px;padding:12px 32px;letter-spacing:1px;text-decoration:none}

/* features */
.features{position:absolute;top:1580px;left:100px;width:1000px;display:flex;gap:44px}
.feature{width:304px;border-bottom:2px solid var(--line);padding-bottom:20px}
.feature-icon{width:58px;height:58px;background:var(--blue);display:flex;align-items:center;justify-content:center;border-radius:4px}
.feature h3{font-size:20px;font-weight:500;margin-top:20px}
.feature p{font-size:12px;color:var(--muted);margin-top:10px}
.more-link{display:flex;align-items:center;gap:8px;margin-top:14px;font-size:12px;font-weight:700;color:var(--blue)}
.more-dot{width:16px;height:16px;border-radius:50%;background:var(--blue)}

/* news */
.news{position:absolute;top:1880px;left:0;width:1200px;height:460px;background:var(--light);padding-top:50px}
.news h2{text-align:center;font-size:36px;font-weight:400;letter-spacing:1px}
.news-grid{display:flex;gap:20px;margin:60px 0 0 100px}
.news-item{width:232px;height:220px;position:relative}
.news-caption{position:absolute;left:12px;bottom:36px;background:var(--white);font-size:12px;padding:6px 10px;width:170px}
.news-date{position:absolute;left:12px;bottom:12px;background:var(--blue);color:var(--white);font-size:11px;font-weight:700;padding:4px 10px}

/* footer */
.site-footer{position:absolute;top:2340px;left:0;width:1200px;height:156px;background:var(--footer);color:var(--footer-text)}
.footer-row{display:flex;align-items:center;justify-content:space-between;padding:32px 100px 0;font-size:13px}
.socials{display:flex;gap:10px}
.socials span{width:30px;height:30px;border-radius:50%;background:#454a52}
.footer-item{display:flex;align-items:center;gap:14px;width:240px}
.footer-icon{width:36px;height:36px;border-radius:50%;background:#3a3e45;display:flex;align-items:center;justify-content:center;flex-shrink:0}
.copyright{position:absolute;bottom:0;left:0;width:1200px;border-top:1px solid #363a40;text-align:center;font-size:12px;padding:14px 0}
</style>
</head>
<body>

<header class="site-header">
  <div class="brand"><span class="brand-mark"></span><span class="brand-name">Brimlow OrthoLink IT</span></div>
  <div class="search">Search
    <svg width="14" height="14" viewBox="0 0 14 14"><circle cx="6" cy="6" r="4.5" fill="none" stroke="#888" stroke-width="1.5"/><line x1="9.5" y1="9.5" x2="13" y2="13" stroke="#888" stroke-width="1.5"/></svg>
  </div>
  <div class="contact-top">
    <div><strong>Have any Question?</strong><span>+1 555 0148 2290</span></div>
    <div class="round-icon"><svg width="18" height="18" viewBox="0 0 24 24"><path d="M6.6 10.8a15.1 15.1 0 0 0 6.6 6.6l2.2-2.2a1 1 0 0 1 1-.25 11.4 11.4 0 0 0 3.6.57 1 1 0 0 1 1 1V20a1 1 0 0 1-1 1A17 17 0 0 1 3 4a1 1 0 0 1 1-1h3.5a1 1 0 0 1 1 1c0 1.25.2 2.45.57 3.57a1 1 0 0 1-.25 1z" fill="#fff"/></svg></div>
  </div>
</header>

<nav class="main-nav">
  <a class="active" href="#">HOME</a>
  <a href="#">ABOUT ORTHOLINK IT</a>
  <a href="#">OUR SERVICES</a>
  <a href="#">TECHNOLOGY</a>
  <a href="#">NEWS</a>
  <a href="#">CONTACT US</a>
</nav>

<section class="hero" role="img" aria-label="Photo of a dentist holding a large model tooth and a dental mirror">
  <div class="hero-copy">
    <h1>Service to Dental Professionals</h1>
    <p>Reliable systems, secure networks and support so your practice keeps running.</p>
  </div>
  <div class="hero-arrow prev"><svg width="12" height="20" viewBox="0 0 12 20"><path d="M10 2 2 10l8 8" fill="none" stroke="#fff" stroke-width="2.5"/></svg></div>
  <div class="hero-arrow next"><svg width="12" height="20" viewBox="0 0 12 20"><path d="M2 2l8 8-8 8" fill="none" stroke="#fff" stroke-width="2.5"/></svg></div>
</section>

<section class="services" style="height:500px">
  <div class="services-head">
    <h2>Our Services</h2>
    <p>We install, manage and support every piece of technology in your dental office, from chairside screens to servers and secure cloud storage. Our team keeps your systems fast, safe and always ready for patients, with clear plans and friendly local support.</p>
  </div>
  <div class="service-cards">
    <div class="service-card">
      <div class="service-photo" role="img" aria-label="Photo of a meeting room with a presentation screen" style="background:linear-gradient(135deg,#8a6a3f,#d3a85f 55%,#5a4a3a)"></div>
      <h3>Audio Visual</h3>
      <div class="row"><p>Screens, sound and displays set up for clinics and patient rooms.</p>
        <svg width="10" height="16" viewBox="0 0 10 16"><path d="M2 2l6 6-6 6" fill="none" stroke="#999" stroke-width="2"/></svg></div>
    </div>
    <div class="service-card">
      <div class="service-photo" role="img" aria-label="Illustration of networked computers" style="background:linear-gradient(135deg,#d9eef7,#6fb3d6 60%,#2f7fb0)"></div>
      <h3>Computer systems and networks</h3>
      <div class="row"><p>Workstations and networks built and maintained for your practice.</p>
        <svg width="10" height="16" viewBox="0 0 10 16"><path d="M2 2l6 6-6 6" fill="none" stroke="#999" stroke-width="2"/></svg></div>
    </div>
    <div class="service-card">
      <div class="service-photo" role="img" aria-label="Illustration of cloud data backup" style="background:linear-gradient(135deg,#1c2530,#4b5a6a 60%,#9aa6b2)"></div>
      <h3>Cloud services of data backup</h3>
      <div class="row"><p>Secure off-site backup and data center hosting for patient records.</p>
        <svg width="10" height="16" viewBox="0 0 10 16"><path d="M2 2l6 6-6 6" fill="none" stroke="#999" stroke-width="2"/></svg></div>
    </div>
  </div>
</section>

<section class="welcome" role="img" aria-label="Red band over a faint city skyline photo" style="background:linear-gradient(180deg,#ec1f27,#d81c24)">
  <h2>WELCOME TO ORTHOLINK IT</h2>
  <p>We are a technology partner built only for dental offices. From the front desk to the operatory, we plan, install and look after the systems your team relies on every day. Our technicians know dental software, imaging and compliance, so you get fewer surprises and faster fixes. Focus on your patients while we keep the technology running smoothly behind the scenes.</p>
  <a class="btn-outline" href="#">KNOW MORE</a>
</section>

<section class="features">
  <div class="feature">
    <div class="feature-icon"><svg width="28" height="28" viewBox="0 0 24 24"><circle cx="12" cy="12" r="4" fill="none" stroke="#fff" stroke-width="2"/><path d="M12 2v4M12 18v4M2 12h4M18 12h4M5 5l3 3M16 16l3 3M5 19l3-3M16 8l3-3" stroke="#fff" stroke-width="2"/></svg></div>
    <h3>Manage Services</h3>
    <p>Proactive monitoring, updates and maintenance for every device in your office, billed as one simple monthly plan.</p>
    <div class="more-link">CLICK HERE <span class="more-dot"></span></div>
  </div>
  <div class="feature">
    <div class="feature-icon"><svg width="28" height="28" viewBox="0 0 24 24"><rect x="3" y="3" width="18" height="18" rx="3" fill="none" stroke="#fff" stroke-width="2"/><path d="M12 7v10M7 12h10" stroke="#fff" stroke-width="2"/></svg></div>
    <h3>Support and Service</h3>
    <p>Fast help desk and on-site visits from technicians who understand dental software and imaging equipment.</p>
    <div class="more-link">CLICK HERE <span class="more-dot"></span></div>
  </div>
  <div class="feature">
    <div class="feature-icon"><svg width="28" height="28" viewBox="0 0 24 24"><circle cx="12" cy="8" r="4" fill="none" stroke="#fff" stroke-width="2"/><path d="M4 21c0-4 4-7 8-7s8 3 8 7" fill="none" stroke="#fff" stroke-width="2"/></svg></div>
    <h3>Dental Professionals</h3>
    <p>Solutions shaped around dentists, hygienists and front desk staff so every workflow stays smooth and secure.</p>
    <div class="more-link">CLICK HERE <span class="more-dot"></span></div>
  </div>
</section>

<section class="news">
  <h2>LATEST NEWS</h2>
  <div class="news-grid">
    <div class="news-item" role="img" aria-label="Photo of a person working at a laptop" style="background:linear-gradient(135deg,#cfd6dc,#8d9aa6)"><span class="news-caption">Sed ut perspiciatis unde</span><span class="news-date">15 AUG 2016</span></div>
    <div class="news-item" role="img" aria-label="Photo of a group of colleagues" style="background:linear-gradient(135deg,#e2d6c8,#9e8a76)"><span class="news-caption">Sed ut perspiciatis unde</span><span class="news-date">15 AUG 2016</span></div>
    <div class="news-item" role="img" aria-label="Photo of a smiling professional" style="background:linear-gradient(135deg,#f0e6da,#c0a890)"><span class="news-caption">Sed ut perspiciatis unde</span><span class="news-date">15 AUG 2016</span></div>
    <div class="news-item" role="img" aria-label="Photo of business people with umbrellas" style="background:linear-gradient(135deg,#3c5f86,#1a2a3e)"><span class="news-caption">Sed ut perspiciatis unde</span><span class="news-date">15 AUG 2016</span></div>
  </div>
</section>

<footer class="site-footer">
  <div class="footer-row">
    <div class="socials"><span></span><span></span><span></span><span></span></div>
    <div class="footer-item">
      <div class="footer-icon"><svg width="14" height="18" viewBox="0 0 14 18"><path d="M7 1a6 6 0 0 0-6 6c0 4.5 6 10 6 10s6-5.5 6-10a6 6 0 0 0-6-6z" fill="none" stroke="#b9bcc2" stroke-width="1.6"/><circle cx="7" cy="7" r="2" fill="#b9bcc2"/></svg></div>
      <span>12 Brimlow Lane, Suite 4,<br>Harbor City</span>
    </div>
    <div class="footer-item">
      <div class="footer-icon"><svg width="16" height="16" viewBox="0 0 24 24"><path d="M6.6 10.8a15.1 15.1 0 0 0 6.6 6.6l2.2-2.2a1 1 0 0 1 1-.25 11.4 11.4 0 0 0 3.6.57 1 1 0 0 1 1 1V20a1 1 0 0 1-1 1A17 17 0 0 1 3 4a1 1 0 0 1 1-1h3.5a1 1 0 0 1 1 1c0 1.25.2 2.45.57 3.57a1 1 0 0 1-.25 1z" fill="#b9bcc2"/></svg></div>
      <span>Phone :<br>+1 555 0148 2290</span>
    </div>
    <div class="footer-item">
      <div class="footer-icon"><svg width="16" height="12" viewBox="0 0 16 12"><rect x="1" y="1" width="14" height="10" fill="none" stroke="#b9bcc2" stroke-width="1.5"/><path d="M1 1l7 6 7-6" fill="none" stroke="#b9bcc2" stroke-width="1.5"/></svg></div>
      <span>E-mail :<br>hello@ortholink-it.example</span>
    </div>
  </div>
  <div class="copyright">© Copyright 2016 Brimlow OrthoLink IT Inc. All Rights Reserved.</div>
</footer>

</body>
</html>
```